Vegan bakery needs business card

We need a business card design for my vegan bakery in Philadelphia Pa. We create amazing whole food plant based cuisine that is egg and dairy free. We use fruits, vegetables, healing herbs, nuts, natural sugars (date, turbinado, agave) and non bleached flours in our creations. Due to demand and interest in the Philadelphia area we created a late night vegan dessert delivery service named Bramble Vegan. We are the only business providing delicious vegan desserts delivered to your door at 1am!! We would like to see designs that use the color scheme in the logo. The final design should communicate the benefits of our products: dairy/egg free, plant based, healing herbs, amazing food.

```html
<!DOCTYPE html>
<html lang="en">
<head>
<meta charset="utf-8">
<title>Bramble Vegan — Business Card</title>
<link rel="stylesheet" href="https://fonts.googleapis.com/css2?family=Questrial&family=Comfortaa:wght@600&display=swap">
<style>
  :root {
    --page: #e9e5e1;
    --card-top: #f4f3f2;
    --card-bottom: #dcdad8;
    --brand-red: #d4503a;
    --leaf-green: #3e9a3a;
    --ink-dark: #3a3634;
    --band-dark: #1e1c1c;
    --text-light: #cfc8c3;
    --sans: "Questrial", "Century Gothic", sans-serif;
    --round: "Comfortaa", sans-serif;
  }
  html, body {
    margin: 0;
    width: 1200px;
    height: 970px;
    overflow: hidden;
    background: var(--page);
  }
  .business-card {
    position: absolute;
    left: 80px;
    top: 189px;
    width: 1040px;
    height: 592px;
    border-radius: 26px;
    overflow: hidden;
    background: linear-gradient(170deg, var(--card-top), var(--card-bottom));
    box-shadow: 0 10px 30px rgba(0,0,0,.18);
    font-family: var(--sans);
  }
  .panel-art {
    position: absolute;
    inset: 0;
  }
  .brand {
    position: absolute;
    left: 60px;
    top: 150px;
    width: 380px;
    text-align: center;
  }
  .brand-name {
    display: inline-flex;
    align-items: center;
    gap: 12px;
    font-size: 38px;
    color: var(--brand-red);
    white-space: nowrap;
  }
  .brand-dot {
    width: 20px;
    height: 20px;
    border-radius: 50%;
    background: var(--brand-red);
  }
  .tagline {
    position: absolute;
    left: 95px;
    top: 292px;
    width: 310px;
    text-align: center;
    font-family: var(--round);
    font-weight: 600;
    font-size: 23px;
    line-height: 27px;
    color: var(--leaf-green);
  }
  .person {
    position: absolute;
    right: 42px;
    top: 66px;
    text-align: right;
  }
  .person-name {
    font-size: 33px;
    color: var(--brand-red);
    line-height: 38px;
  }
  .person-role {
    font-size: 24px;
    color: var(--ink-dark);
    line-height: 28px;
  }
  .contact {
    position: absolute;
    right: 44px;
    top: 362px;
    text-align: right;
    color: var(--text-light);
    font-size: 24px;
  }
  .address p { margin: 0; line-height: 33px; }
  .lines { margin-top: 24px; }
  .line {
    display: flex;
    justify-content: flex-end;
    align-items: center;
    gap: 10px;
    line-height: 31px;
  }
  .line svg { width: 24px; height: 24px; }
</style>
</head>
<body>
  <div class="business-card">
    <svg class="panel-art" viewBox="0 0 1040 592" preserveAspectRatio="none" aria-hidden="true">
      <rect x="0" y="560" width="1040" height="32" fill="var(--band-dark)"/>
      <polygon points="560,592 760,330 1040,330 1040,592" fill="var(--band-dark)"/>
      <polygon points="520,592 740,304 752,304 532,592" fill="var(--brand-red)"/>
      <rect x="0" y="548" width="528" height="6" fill="var(--brand-red)"/>
    </svg>

    <div class="brand">
      <span class="brand-name"><span class="brand-dot"></span>Bramble Vegan</span>
    </div>
    <div class="tagline">100% vegan<br>100% delicious</div>

    <div class="person">
      <div class="person-name">Nora Whitfield</div>
      <div class="person-role">Director of Marketing</div>
    </div>

    <div class="contact">
      <div class="address">
        <p>PO Box 418, Walnut Street</p>
        <p>Philadelphia, PA 19106</p>
      </div>
      <div class="lines">
        <div class="line">215-555-0187
          <svg viewBox="0 0 24 24"><circle cx="12" cy="12" r="11" fill="var(--text-light)"/><path d="M6,10 Q12,5 18,10 L16,12 L14,10 L10,10 L8,12 Z M7,13 h10 v5 h-10 Z" fill="var(--band-dark)"/></svg>
        </div>
        <div class="line">hello@bramblevegan.com
          <svg viewBox="0 0 24 24"><circle cx="12" cy="12" r="11" fill="var(--text-light)"/><rect x="6" y="8" width="12" height="9" fill="var(--band-dark)"/><path d="M6,8 L12,13 L18,8" stroke="var(--text-light)" stroke-width="1.2" fill="none"/></svg>
        </div>
        <div class="line">www.bramblevegan.com
          <svg viewBox="0 0 24 24"><circle cx="12" cy="12" r="11" fill="var(--text-light)"/><circle cx="12" cy="12" r="7" fill="var(--band-dark)"/><path d="M5,12 h14 M12,5 v14" stroke="var(--text-light)" stroke-width="1"/></svg>
        </div>
      </div>
    </div>
  </div>
</body>
</html>
```